Business Card Design - ChoiceCraft

Looking for creative, modern design, two sided for ChoiceCraft that is consistent with color and feel of website www.choicecraftpro.net.
Updates

Back of card will be used to promote products or have a quote revolving around decisions, change, leadership, innovation, creativity. Back should also have space to promote website, but optional to use the icon. Front of the card will need to use the icon and have standard place for name, job title, phone and email. We are not looking to put a mailing address or fax. Also want space to place a few words/phrase explaining what we do...such as individual growth and organizational development or tools, training, information...in addition, want the facebook icon small on the front somewhere as we are also on facebook.

Vector file uploaded of icon.

Target Market(s)

Professional coaching for individual growth and organizational development

Industry/Entity Type

Business

Requirements
Must have
• Icon...see attached.

```html
<!DOCTYPE html>
<html lang="en">
<head>
<meta charset="utf-8">
<title>ChoiceCraft – Business Card</title>
<link href="https://fonts.googleapis.com/css2?family=Source+Sans+3:wght@400;600;700&family=Arimo:wght@400;700&display=swap" rel="stylesheet">
<style>
  :root {
    --stage: #202020;
    --navy: #1d3592;
    --royal: #1f5cc4;
    --cyan: #08a6e4;
    --sky: #39c4f2;
    --back-deep: #0a6fc0;
    --back-mid: #1593da;
    --ink: #ffffff;
    --ink-soft: rgba(255,255,255,0.88);
    --rule: rgba(190,235,255,0.7);
  }
  * { margin: 0; padding: 0; box-sizing: border-box; }
  html, body { width: 1200px; height: 757px; overflow: hidden; background: var(--stage); }
  .canvas {
    width: 1200px; height: 757px;
    display: flex; align-items: center; justify-content: center; gap: 30px;
  }
  .card {
    width: 560px; height: 330px; border-radius: 20px;
    position: relative; overflow: hidden; color: var(--ink);
  }
  /* Front */
  .card--front {
    background: linear-gradient(160deg, var(--navy) 0%, var(--royal) 22%, var(--cyan) 48%, var(--royal) 78%, var(--navy) 100%);
    font-family: "Source Sans 3", sans-serif;
  }
  .brand {
    position: absolute; left: 40px; top: 72px; width: 200px;
    display: flex; flex-direction: column; align-items: center; gap: 14px;
  }
  .brand__mark {
    width: 96px; height: 96px; border-radius: 50%;
    background: radial-gradient(circle at 40% 35%, #e6f4fb, #8fb8d8 60%, #3f7fc2);
  }
  .brand__name { font-size: 20px; font-weight: 400; letter-spacing: 0.3px; color: var(--ink); }
  .divider {
    position: absolute; left: 262px; top: 48px; width: 2px; height: 160px;
    background: linear-gradient(to bottom, transparent, var(--rule), transparent);
  }
  .identity { position: absolute; left: 284px; top: 50px; }
  .identity__name { font-size: 24px; font-weight: 700; line-height: 1.1; }
  .identity__title { font-size: 17px; color: var(--ink-soft); margin-top: 4px; margin-bottom: 14px; }
  .contact { list-style: none; font-size: 15px; line-height: 1.32; color: var(--ink-soft); }
  .contact li { display: flex; align-items: center; gap: 6px; }
  .contact svg { width: 12px; height: 12px; flex: none; }
  .contact .social-square { width: 10px; height: 10px; background: var(--ink-soft); border-radius: 2px; margin: 0 1px; }
  .tagline {
    position: absolute; left: 0; right: 0; bottom: 42px;
    text-align: center; font-size: 18px; line-height: 1.35; color: var(--ink);
  }
  /* Back */
  .card--back {
    background: radial-gradient(ellipse at 48% 42%, var(--sky) 0%, var(--back-mid) 45%, var(--back-deep) 100%);
    font-family: "Arimo", sans-serif;
  }
  .quotes { list-style: none; position: absolute; left: 36px; top: 26px; right: 30px; }
  .quote { margin-bottom: 10px; font-size: 14.5px; line-height: 1.35; }
  .quote__text::before { content: "\201C"; font-weight: 700; font-size: 20px; line-height: 0; margin-right: 3px; vertical-align: -4px; }
  .quote__text::after { content: "\201D"; font-weight: 700; font-size: 20px; line-height: 0; margin-left: 3px; vertical-align: -8px; }
  .quote__author { display: block; font-weight: 700; padding-left: 10px; }
  .back-mark {
    position: absolute; right: 40px; bottom: 26px; width: 120px; height: 120px;
    border-radius: 50%; background: rgba(20, 80, 170, 0.35);
  }
</style>
</head>
<body>
<main class="canvas">
  <section class="card card--front" aria-label="Business card front">
    <div class="brand">
      <div class="brand__mark"></div>
      <span class="brand__name">ChoiceCraft</span>
    </div>
    <div class="divider"></div>
    <div class="identity">
      <h1 class="identity__name">Your Name</h1>
      <p class="identity__title">Title</p>
      <ul class="contact">
        <li><svg viewBox="0 0 12 12"><circle cx="6" cy="6" r="5.3" fill="none" stroke="#fff" stroke-width="1.2"/><path d="M4 3.2l1 1.4-.6.8c.4.9 1 1.5 1.9 1.9l.8-.6 1.4 1-.6 1c-2.4-.2-4.4-2.2-4.6-4.6z" fill="#fff"/></svg>123-456-789</li>
        <li><svg viewBox="0 0 12 12"><circle cx="6" cy="6" r="6" fill="#fff"/><rect x="3" y="4" width="6" height="4.2" fill="#1f5cc4"/><path d="M3 4l3 2.3L9 4" stroke="#fff" stroke-width=".8" fill="none"/></svg>info@choicecraftpro.net</li>
        <li><svg viewBox="0 0 12 12"><circle cx="6" cy="6" r="5.3" fill="none" stroke="#fff" stroke-width="1.2"/><ellipse cx="6" cy="6" rx="2.2" ry="5.3" fill="none" stroke="#fff" stroke-width=".9"/><path d="M.8 6h10.4M1.8 3.5h8.4M1.8 8.5h8.4" stroke="#fff" stroke-width=".8"/></svg>www.choicecraftpro.net</li>
        <li><span class="social-square"></span>/choicecraftpro</li>
      </ul>
    </div>
    <p class="tagline">Supporting Individual Growth And Organizational<br>Development Or Tools, Training, Information</p>
  </section>

  <section class="card card--back" aria-label="Business card back">
    <div class="back-mark"></div>
    <ul class="quotes">
      <li class="quote"><span class="quote__text">Try not to become a man of success, but rather a man of value.</span><span class="quote__author">- Alden Marsh</span></li>
      <li class="quote"><span class="quote__text">The only constant is change.</span><span class="quote__author">- Theron Vale</span></li>
      <li class="quote"><span class="quote__text">We are what we repeatedly do. Excellence is not an act, it is a habit.</span><span class="quote__author">- Ariston Pell</span></li>
      <li class="quote"><span class="quote__text">Simplicity is the ultimate sophistication.</span><span class="quote__author">- Lorenzo Davani</span></li>
      <li class="quote"><span class="quote__text">Life is not fair - get used to it.</span><span class="quote__author">- Wes Harlan</span></li>
    </ul>
  </section>
</main>
</body>
</html>
```